New, modern business card for growing audiology practice

We need a new business card for our audiology practice. Our logo and website have recently changed (more modern) and we want our business cards to reflect this change.
We conduct hearing tests, perform earwax removals, and fit & dispense hearing aids to our patients. We are a family owned practice in which the owner is the one who works directly with the patient. I have attached logos in various formats to use, as well as two ideas I found on this website; as well as a scanned copy of our current logo. Good luck!

Industry/Entity Type

Business

Contact Information for Business Card

Company name: Tolvera Hearing Center
Provider name: Peter Wolstenby, Au.D. F/NSB
Phone number: (555) 683-5127
Address: 837 W. Lindell Ave. Brenwick Falls, ZN 90417
email: tolverahearing@postvane.com
website: tolverahearing.com

Colors
000000
aaaaaa
dbdbdb
cacaca
9bcb3c
afd23c
cadf82
b1b1b1

Requirements
Must have
• My card must include information in the "details" section. In the attached images, I found a few that I liked and I would like to model after - "brisky bouncin'" and "Sound Method Center".
• Must be horizontal.
• Must include logos provided. I uploaded them in various file formats and various ways.
• Must match logo font, if possible, if not, please get as close as you can.
Nice to have
• I really like the idea of having a color on one side with just the logo and company name and the contact information and provider name on the other side. I also really like the idea of having the main color dominating on the logo/company side with accent of that same color on the contact side of the card.
Should not have
• Must not be vertical.

```html
<!DOCTYPE html>
<html lang="en">
<head>
<meta charset="utf-8">
<title>Tolvera Hearing Center – Business Card</title>
<link rel="stylesheet" href="https://fonts.googleapis.com/css2?family=Lato:wght@400&family=Roboto:wght@400;500&family=Roboto+Condensed:wght@700&display=swap">
<style>
  :root {
    --backdrop: #e6e4e0;
    --card-white: #f4f4f4;
    --brand-green: #6f9f35;
    --ink: #141414;
    --black: #000000;
    --white: #ffffff;
  }
  * { margin: 0; padding: 0; box-sizing: border-box; }
  html, body {
    width: 1200px;
    height: 960px;
    overflow: hidden;
    background: var(--backdrop);
  }
  .stage {
    position: relative;
    width: 1200px;
    height: 960px;
  }
  .card {
    position: absolute;
    width: 600px;
    height: 343px;
    overflow: hidden;
  }
  .card--front { left: 314px; top: 113px; background: var(--card-white); }
  .card--back  { left: 311px; top: 472px; background: var(--black); }

  .front-sweep {
    position: absolute;
    inset: 0;
  }

  .wordmark {
    position: absolute;
    display: flex;
    align-items: center;
    font-family: "Lato", "Gill Sans", sans-serif;
    font-weight: 400;
    white-space: nowrap;
    letter-spacing: 0.2px;
  }
  .wordmark__dot {
    border-radius: 50%;
    background: var(--brand-green);
    flex: none;
  }
  .card--front .wordmark {
    left: 40px;
    top: 160px;
    font-size: 17px;
    color: var(--ink);
  }
  .card--front .wordmark__dot { width: 14px; height: 14px; margin-right: 9px; }

  .card--back .wordmark {
    left: 0;
    right: 0;
    top: 154px;
    justify-content: center;
    font-size: 29px;
    color: var(--white);
  }
  .card--back .wordmark__dot { width: 22px; height: 22px; margin-right: 14px; }

  .contact {
    position: absolute;
    right: 27px;
    top: 92px;
    text-align: right;
    color: var(--white);
    font-family: "Roboto", Arial, sans-serif;
    font-size: 14px;
    line-height: 18px;
  }
  .contact__name {
    font-family: "Roboto Condensed", "Arial Narrow", sans-serif;
    font-weight: 700;
    font-size: 21px;
    line-height: 24px;
  }
  .contact__title {
    font-family: "Roboto", Arial, sans-serif;
    font-weight: 500;
    font-size: 15px;
    line-height: 20px;
    margin-bottom: 12px;
  }
  .contact__address { margin-bottom: 10px; }
  .contact__line {
    display: flex;
    justify-content: flex-end;
    align-items: center;
    gap: 6px;
    line-height: 19px;
  }
  .contact__icon { width: 12px; height: 12px; flex: none; }

  .web {
    position: absolute;
    left: 0;
    right: 0;
    top: 287px;
    text-align: center;
    font-family: "Roboto", Arial, sans-serif;
    font-size: 14px;
    letter-spacing: 4px;
    color: var(--white);
  }
  .web__domain { color: var(--brand-green); }
</style>
</head>
<body>
<main class="stage">

  <section class="card card--front" aria-label="Card front">
    <svg class="front-sweep" width="600" height="343" viewBox="0 0 600 343" aria-hidden="true">
      <path d="M286 0 Q430 171.5 286 343 L600 343 L600 0 Z" fill="var(--brand-green)"/>
      <path d="M281 0 Q426 171.5 281 343" fill="none" stroke="var(--white)" stroke-width="3"/>
      <path d="M274 0 Q418 171.5 274 343" fill="none" stroke="var(--black)" stroke-width="7"/>
      <path d="M266 0 Q402 171.5 266 343" fill="none" stroke="var(--black)" stroke-width="3"/>
    </svg>

    <div class="wordmark">
      <span class="wordmark__dot"></span>
      <span class="wordmark__text">TOLVERA HEARING CENTER</span>
    </div>

    <div class="contact">
      <p class="contact__name">PETER WOLSTENBY</p>
      <p class="contact__title">AU.D. F/NSB</p>
      <p class="contact__address">837 W. Lindell Ave.<br>Brenwick Falls, ZN 90417</p>
      <p class="contact__line">(555) 683-5127
        <svg class="contact__icon" viewBox="0 0 12 12" aria-hidden="true"><path d="M2.4 1 L4.3 1 L5 3.6 L3.8 4.6 Q5 7.2 7.4 8.2 L8.4 7 L11 7.7 L11 9.6 Q10.6 11 9.2 11 Q1 10 1 2.8 Q1 1.4 2.4 1 Z" fill="var(--white)"/></svg>
      </p>
      <p class="contact__line">tolverahearing@postvane.com
        <svg class="contact__icon" viewBox="0 0 12 12" aria-hidden="true"><rect x="0.5" y="2.5" width="11" height="7.5" fill="var(--white)"/><path d="M0.5 2.5 L6 7 L11.5 2.5" fill="none" stroke="var(--brand-green)" stroke-width="1"/></svg>
      </p>
      <p class="contact__line">tolverahearing.com
        <svg class="contact__icon" viewBox="0 0 12 12" aria-hidden="true"><circle cx="6" cy="6" r="5.5" fill="var(--white)"/><path d="M1 6 H11 M6 0.5 Q3 6 6 11.5 M6 0.5 Q9 6 6 11.5" fill="none" stroke="var(--brand-green)" stroke-width="0.9"/></svg>
      </p>
    </div>
  </section>

  <section class="card card--back" aria-label="Card back">
    <div class="wordmark">
      <span class="wordmark__dot"></span>
      <span class="wordmark__text">TOLVERA HEARING CENTER</span>
    </div>
    <p class="web">www.<span class="web__domain">tolverahearing</span>.com</p>
  </section>

</main>
</body>
</html>
```